Automotive component supplier needs a business card design

We need a business card design for our company called Velran Global Components Ltd based in the UK. We are a supplier of interior and exterior components to premium car manufacturers such as Corvel Ashby, Hadley Fenn, Marquist and Tavarelli. We would like to see a modern business card design that uses the colour blue.

Target Market(s)

Premium automotive car manufacturers.

Industry/Entity Type

Automotive

Contact Information for Business Card

Company Name : Velran Global Components Limited
Address: 17 Marlow Yard, Upper Heath, Warwick, CV31 8QL, United Kingdom
Web Address : www.velrancomponents-example.co.uk

Font styles to use
Other font styles liked:
• Helvetica

Colors
3176b5
0255a3
85acd3
cfdeed
cee9f5
85cae6
34a6d7
0692cd
9bcb3c

Requirements
Must have
• Clear company logo and a mixture of blue colours.
Nice to have
• A high quality modern image.
Should not have
• Multiple colours.

```html
<!DOCTYPE html>
<html lang="en">
<head>
<meta charset="utf-8">
<title>Velran Global Components – Business Card</title>
<link rel="stylesheet" href="https://fonts.googleapis.com/css2?family=Arimo:wght@400;700&display=swap">
<style>
  :root {
    --blue-deep: #0255a3;
    --blue-brand: #0692cd;
    --blue-mid: #34a6d7;
    --blue-light: #85cae6;
    --green: #9bcb3c;
    --white: #ffffff;
    --ink-soft: #ffffff;
    --stage: #e9edf1;
  }
  * { box-sizing: border-box; margin: 0; padding: 0; }
  html, body {
    width: 1200px; height: 950px; overflow: hidden;
    background: var(--stage);
    font-family: "Arimo", Helvetica, Arial, sans-serif;
  }
  .sheet {
    position: relative; width: 1200px; height: 950px;
    display: flex; flex-direction: column; align-items: center;
    justify-content: center; gap: 40px;
  }
  .card {
    position: relative; width: 760px; height: 420px;
    overflow: hidden; box-shadow: 0 6px 18px rgba(0,0,0,.18);
  }

  /* Front */
  .card--front { background: var(--white); }
  .brand { position: absolute; left: 58px; top: 96px; color: var(--blue-brand); font-weight: 700; }
  .brand__name { font-size: 84px; letter-spacing: 4px; line-height: 1; }
  .brand__sub { font-size: 17px; letter-spacing: 2.6px; margin-top: 6px; }
  .person { position: absolute; right: 70px; top: 70px; text-align: right; }
  .person__name { color: var(--blue-brand); font-weight: 700; font-size: 22px; letter-spacing: .5px; }
  .person__role { color: var(--green); font-size: 16px; margin-top: 6px; }
  .band {
    position: absolute; left: 0; right: 0; top: 220px; height: 140px;
    background: linear-gradient(90deg, var(--blue-deep) 0%, var(--blue-brand) 35%, var(--blue-mid) 100%);
  }
  .band__accent {
    position: absolute; right: 24px; top: -28px; width: 28px; height: 28px;
    background: var(--green); border: 3px solid var(--white);
  }
  .contact { position: absolute; left: 58px; top: 30px; list-style: none; color: var(--ink-soft); font-size: 16px; }
  .contact li { display: flex; align-items: center; gap: 10px; height: 27px; }
  .contact svg { width: 14px; height: 14px; fill: var(--white); flex: none; }
  .address { position: absolute; right: 70px; top: 30px; text-align: right; color: var(--ink-soft); font-size: 16px; line-height: 27px; font-style: normal; }
  .web {
    position: absolute; left: 58px; top: 376px; color: var(--blue-deep);
    font-weight: 700; font-size: 16px; letter-spacing: .3px;
  }

  /* Back */
  .card--back { background: var(--green); display: flex; align-items: center; justify-content: center; }
  .brand--reverse { position: static; color: var(--white); text-align: left; }
  .brand--reverse .brand__name { font-size: 110px; letter-spacing: 6px; }
  .brand--reverse .brand__sub { font-size: 22px; letter-spacing: 3.6px; }
</style>
</head>
<body>
<main class="sheet">
  <section class="card card--front" aria-label="Business card front">
    <div class="brand">
      <div class="brand__name">VELRAN</div>
      <div class="brand__sub">GLOBAL COMPONENTS</div>
    </div>
    <div class="person">
      <div class="person__name">DANIEL ORTWAY</div>
      <div class="person__role">CEO / Founder</div>
    </div>
    <div class="band">
      <span class="band__accent"></span>
      <ul class="contact">
        <li><svg viewBox="0 0 24 24" aria-hidden="true"><path d="M6.6 10.8a15.1 15.1 0 0 0 6.6 6.6l2.2-2.2a1 1 0 0 1 1-.25 11.4 11.4 0 0 0 3.6.57 1 1 0 0 1 1 1V20a1 1 0 0 1-1 1A17 17 0 0 1 3 4a1 1 0 0 1 1-1h3.5a1 1 0 0 1 1 1c0 1.25.2 2.46.57 3.6a1 1 0 0 1-.25 1z"/></svg>01926 555 0147</li>
        <li><svg viewBox="0 0 24 24" aria-hidden="true"><path d="M7 1h10a2 2 0 0 1 2 2v18a2 2 0 0 1-2 2H7a2 2 0 0 1-2-2V3a2 2 0 0 1 2-2zm0 3v14h10V4z"/></svg>07700 900 318</li>
        <li><svg viewBox="0 0 24 24" aria-hidden="true"><path d="M2 5h20v14H2zm2 2v.5l8 5 8-5V7zm0 2.8V17h16V9.8l-8 5z"/></svg>daniel@velrancomponents-example.co.uk</li>
      </ul>
      <address class="address">17 Marlow Yard, Upper Heath<br>Warwick, CV31 8QL<br>United Kingdom</address>
    </div>
    <div class="web">www.velrancomponents-example.co.uk</div>
  </section>

  <section class="card card--back" aria-label="Business card back">
    <div class="brand brand--reverse">
      <div class="brand__name">VELRAN</div>
      <div class="brand__sub">GLOBAL COMPONENTS</div>
    </div>
  </section>
</main>
</body>
</html>
```